"Harbor Builders" is a residential building company and needs a new business card design and may re

We would like a redesign based on the existing logo, and would like to see a new font as well. We are bespoke home builders who build sustainable energy efficient homes.

Industry/Entity Type

Construction

Contact Information for Business Card

Business card size 40mm x 90mm

Colors

Designer to choose colors to be used in the design.

```html
<!DOCTYPE html>
<html lang="en">
<head>
<meta charset="utf-8">
<title>Harbor Builders – Business Card</title>
<link href="https://fonts.googleapis.com/css2?family=Ubuntu:wght@500;700&family=Arimo:wght@400&display=swap" rel="stylesheet">
<style>
  :root {
    --gold: #977b2e;
    --gold-text: #8f742a;
    --paper: #f3f3f3;
    --ink-grey: #6b6b6b;
    --band-grey: #6d6d6f;
    --backdrop: #3b3b3b;
    --white: #ffffff;
  }
  html, body {
    margin: 0;
    padding: 0;
    width: 1200px;
    height: 960px;
    overflow: hidden;
    background: var(--backdrop);
  }
  .canvas {
    position: relative;
    width: 1200px;
    height: 960px;
  }
  .card {
    position: absolute;
    left: 270px;
    width: 660px;
    overflow: hidden;
  }
  /* Front */
  .card-front {
    top: 73px;
    height: 377px;
    background: var(--gold);
    color: var(--white);
  }
  .front-brand {
    position: absolute;
    left: 0;
    right: 0;
    top: 270px;
    margin: 0;
    text-align: center;
    font-family: "Ubuntu", sans-serif;
    font-weight: 700;
    font-size: 48px;
    letter-spacing: 1px;
    color: var(--white);
  }
  .front-web {
    position: absolute;
    left: 0;
    right: 0;
    top: 330px;
    text-align: center;
    font-family: "Arimo", sans-serif;
    font-size: 15px;
  }
  /* Back */
  .card-back {
    top: 510px;
    height: 375px;
    background: var(--paper);
  }
  .back-brand {
    position: absolute;
    left: 44px;
    top: 110px;
    display: flex;
    align-items: center;
    gap: 10px;
    margin: 0;
    font-family: "Ubuntu", sans-serif;
    font-weight: 700;
    font-size: 30px;
    color: var(--gold-text);
  }
  .brand-square {
    width: 16px;
    height: 16px;
    background: var(--gold-text);
  }
  .address {
    position: absolute;
    left: 44px;
    top: 208px;
    margin: 0;
    font-family: "Arimo", sans-serif;
    font-style: normal;
    font-size: 15.5px;
    line-height: 21px;
    color: var(--ink-grey);
  }
  .contact-list {
    position: absolute;
    left: 44px;
    top: 259px;
    margin: 0;
    padding: 0;
    list-style: none;
    font-family: "Arimo", sans-serif;
    font-size: 15.5px;
    line-height: 21.5px;
    color: var(--ink-grey);
  }
  .contact-list li {
    display: flex;
    align-items: center;
    gap: 10px;
  }
  .contact-list svg {
    width: 14px;
    height: 14px;
    flex: none;
  }
  .person-name {
    position: absolute;
    right: 53px;
    top: 208px;
    margin: 0;
    font-family: "Ubuntu", sans-serif;
    font-weight: 700;
    font-size: 20px;
    color: var(--gold-text);
  }
  .footer-bands {
    position: absolute;
    left: 0;
    bottom: 0;
    width: 660px;
    height: 40px;
  }
  .registration {
    position: absolute;
    right: 20px;
    top: 341px;
    font-family: "Arimo", sans-serif;
    font-size: 15px;
    color: var(--white);
  }
</style>
</head>
<body>
<main class="canvas">
  <section class="card card-front" aria-label="Card front">
    <h1 class="front-brand">Harbor Builders</h1>
    <div class="front-web">www.harborbuilders.example</div>
  </section>

  <section class="card card-back" aria-label="Card back">
    <h2 class="back-brand"><span class="brand-square"></span>Harbor Builders</h2>

    <address class="address">PO Box 4120 Eastgate<br>LPO Bayview WA 6099</address>

    <ul class="contact-list">
      <li>
        <svg viewBox="0 0 14 14" aria-hidden="true"><path d="M1 5 Q7 0 13 5 L11 6.5 L9.5 5 L4.5 5 L3 6.5 Z M3.5 7 L10.5 7 L12 12 L2 12 Z" fill="#8f742a"/></svg>
        0400 555 018
      </li>
      <li>
        <svg viewBox="0 0 14 14" aria-hidden="true"><rect x="1" y="3" width="12" height="8.5" fill="none" stroke="#6b6b6b" stroke-width="1.2"/><path d="M1 3 L7 8 L13 3" fill="none" stroke="#6b6b6b" stroke-width="1.2"/></svg>
        daniel@harborbuilders.example
      </li>
      <li>
        <svg viewBox="0 0 14 14" aria-hidden="true"><circle cx="7" cy="7" r="5.8" fill="none" stroke="#6b6b6b" stroke-width="1.1"/><ellipse cx="7" cy="7" rx="2.6" ry="5.8" fill="none" stroke="#6b6b6b" stroke-width="1"/><path d="M1.2 7 H12.8 M2.2 4 H11.8 M2.2 10 H11.8" stroke="#6b6b6b" stroke-width="1"/></svg>
        www.harborbuilders.example
      </li>
    </ul>

    <p class="person-name">Daniel Verhoeven</p>

    <svg class="footer-bands" viewBox="0 0 660 40" aria-hidden="true">
      <polygon points="0,15 215,15 200,40 0,40" fill="#6d6d6f"/>
      <polyline points="202,40 216,24 330,24" fill="none" stroke="#ffffff" stroke-width="1.5"/>
      <polygon points="330,5 660,5 660,30 316,30" fill="#977b2e"/>
      <line x1="316" y1="33" x2="660" y2="33" stroke="#6d6d6f" stroke-width="2"/>
    </svg>
    <div class="registration">Registration 40518 ABN: 00 000 000 000</div>
  </section>
</main>
</body>
</html>
```